RM Installations Web Site Design

Need a basic site to show clients a little about what we do. We are a custom audio video company in the high-end residential market. Need a few basic but professional pages to show past projects and products we sell. No e-commerce. Should include my new logo from MarkBazaar.

Industry/Entity Type

Residential

Number of Pages Required

2 page

Font styles to use
Serif
Sans Serif

Colors
f78f20

Requirements
Must have
• Company Logo, Send feedback page
Nice to have
• I have no ideas about design, but I do know what I like and dislike when I see it.

```html
<!DOCTYPE html>
<html lang="en">
<head>
<meta charset="utf-8">
<title>RM Installations</title>
<link href="https://fonts.googleapis.com/css2?family=Oswald:wght@400;500&family=Open+Sans:wght@400;600&display=swap" rel="stylesheet">
<style>
:root{
  --orange:#f78f20;
  --ink:#1d1d1d;
  --text:#333;
  --line:#d8d8d8;
  --footer:#0d0d0d;
  --light-band:#f1f1f1;
  --white:#fff;
}
*{box-sizing:border-box;margin:0;padding:0}
html,body{width:1200px;height:2731px;overflow:hidden;background:var(--white)}
body{position:relative;font-family:"Open Sans",Arial,sans-serif;color:var(--text)}
.abs{position:absolute}
.heading{font-family:"Oswald",Arial,sans-serif;font-weight:500;text-transform:uppercase;color:var(--ink)}
.heading span{color:var(--orange)}
.btn{position:absolute;background:#2a2a2a;color:#fff;font-size:13px;text-transform:uppercase;display:flex;align-items:center;justify-content:center;border-bottom:2px solid #000}

/* hero */
.hero{left:0;top:0;width:1200px;height:601px;background:
  radial-gradient(ellipse 220px 160px at 860px 230px,rgba(255,226,160,.75),rgba(255,226,160,0) 70%),
  radial-gradient(ellipse 140px 120px at 1010px 250px,rgba(255,240,200,.6),rgba(255,240,200,0) 70%),
  radial-gradient(ellipse 260px 220px at 250px 330px,rgba(18,16,20,.95),rgba(18,16,20,.7) 60%,rgba(18,16,20,0) 100%),
  radial-gradient(ellipse 300px 200px at 600px 160px,rgba(255,214,150,.55),rgba(255,214,150,0) 70%),
  linear-gradient(180deg,#8a5a2c 0%,#c08a50 30%,#a86e38 55%,#6a4122 78%,#3a2414 100%)}
.hero-band{left:0;top:471px;width:1200px;height:130px;background:linear-gradient(180deg,rgba(0,0,0,.45),rgba(0,0,0,.7))}
.hero-title{left:133px;top:492px;font-family:"Oswald",Arial,sans-serif;font-weight:500;font-size:29px;color:#fff}
.hero-title span{color:var(--orange)}
.hero-text{left:133px;top:534px;width:402px;font-size:14px;line-height:21px;color:#eee}
.hero-arrows{left:1026px;top:566px}

.nav{left:131px;top:29px;width:938px;height:73px;background:rgba(20,20,20,.85);display:flex;align-items:center}
.brand{width:224px;height:73px;background:#fff;display:flex;align-items:center;gap:10px;padding-left:18px;clip-path:polygon(0 0,100% 0,88% 100%,0 100%)}
.brand-mark{width:30px;height:30px;background:var(--orange)}
.brand-name{font-family:"Oswald",Arial,sans-serif;font-size:19px;line-height:20px;color:#222;text-transform:uppercase}
.nav-links{display:flex;margin-left:28px;height:100%}
.nav-links a{display:flex;align-items:center;padding:0 14px;color:#fff;font-size:14px;text-decoration:none;text-transform:uppercase}
.nav-links a.active{border-top:3px solid var(--orange)}

.divider{position:absolute}

/* services */
.services-title{left:0;width:1200px;top:636px;text-align:center;font-size:33px}
.service-card{position:absolute;top:734px;width:215px;height:269px;border:1px solid var(--line);background:#fff}
.service-photo{position:absolute;left:16px;top:14px;width:183px;height:124px}
.service-name{position:absolute;left:16px;top:148px;font-size:13px;font-weight:600;color:#222}
.service-text{position:absolute;left:16px;top:174px;width:185px;font-size:12px;line-height:18px;color:#555}
.service-card .btn{left:18px;top:224px;width:110px;height:28px}
.side-arrow{position:absolute;top:840px;width:32px;height:32px;background:#ddd;display:flex;align-items:center;justify-content:center}

/* about */
.about{left:0;top:1052px;width:1200px;height:399px;background:var(--orange)}
.about-text{left:133px;top:1178px;width:530px;font-size:12.5px;line-height:21px;color:#fff}
.about-text p+p{margin-top:8px}
.video{left:741px;top:1178px;width:328px;height:178px;background:
  radial-gradient(ellipse 90px 80px at 270px 95px,rgba(40,60,90,.8),rgba(40,60,90,0) 75%),
  radial-gradient(ellipse 120px 60px at 150px 60px,rgba(255,255,255,.9),rgba(255,255,255,0) 80%),
  linear-gradient(180deg,#dfe4ee 0%,#c9d0de 55%,#9aa3b5 100%)}
.video-bar{left:741px;top:1330px;width:328px;height:26px;background:rgba(20,20,20,.85)}
.play{left:888px;top:1245px;width:52px;height:36px;border-radius:9px;background:#d42121}

/* team */
.team-title{left:0;width:1200px;top:1486px;text-align:center;font-size:33px}
.member{position:absolute;top:1582px;width:212px;height:212px}
.diamond{position:absolute;left:31px;top:31px;width:150px;height:150px;transform:rotate(45deg);border:6px solid var(--orange);background:#fff;box-shadow:0 4px 10px rgba(0,0,0,.2)}
.diamond-photo{position:absolute;inset:6px;background:radial-gradient(circle at 50% 50%,#c8c8c8 0%,#7a7a7a 35%,#2a2a2a 80%)}
.diamond.dark{border-color:#2a2a2a}
.diamond.dark .diamond-photo{background:radial-gradient(circle at 50% 50%,#4a4a4a,#222 80%)}
.member-name{position:absolute;top:1815px;width:240px;text-align:center;font-size:16px;color:#333;text-transform:uppercase}
.member-name.active{color:var(--orange)}
.name-rule{left:672px;top:1850px;width:98px;height:2px;background:var(--orange)}

/* products */
.products{left:0;top:1899px;width:1200px;height:224px;background:var(--light-band)}
.products-title{left:0;width:1200px;top:1938px;text-align:center;font-size:33px}
.brand-row{left:130px;top:2028px;width:940px;display:flex;justify-content:space-between;align-items:center}
.brand-row span{font-size:28px;color:#555;display:flex;align-items:center;gap:8px}
.brand-row i{display:inline-block;width:16px;height:16px;border-radius:50%;background:#777}

/* feedback */
.feedback{left:0;top:2123px;width:1200px;height:470px;background:
  radial-gradient(ellipse 260px 160px at 330px 120px,rgba(110,140,170,.35),rgba(110,140,170,0) 75%),
  radial-gradient(ellipse 300px 200px at 1000px 380px,rgba(150,120,90,.3),rgba(150,120,90,0) 75%),
  radial-gradient(ellipse 240px 140px at 760px 100px,rgba(90,110,130,.3),rgba(90,110,130,0) 75%),
  linear-gradient(160deg,#2e2e2e,#161616 60%,#1e1a16)}
.feedback-text{left:133px;top:2255px;width:612px;font-size:13.5px;line-height:23px;color:#fff}
.field{position:absolute;background:#fff;font-size:12px;color:#999;padding:8px 12px}
.submit{position:absolute;left:133px;top:2505px;width:110px;height:28px;background:var(--orange);color:#fff;font-size:13px;font-weight:600;display:flex;align-items:center;justify-content:center}
.share-text{left:797px;top:2255px;width:295px;font-size:12px;line-height:21px;color:#fff}
.social{position:absolute;left:797px;display:flex;align-items:center;gap:18px;color:#fff;font-size:14px}
.social i{width:48px;height:48px;border:2px solid #fff;border-radius:50%;display:flex;align-items:center;justify-content:center}

/* footer */
.footer{left:0;top:2593px;width:1200px;height:104px;background:var(--footer)}
.footer-col{position:absolute;font-size:12.5px;line-height:24px;color:#fff}
.footer-col .row{display:flex;gap:14px;align-items:center}
.footer-brand{left:884px;top:2622px;display:flex;align-items:center;gap:10px}
.footer-brand .brand-mark{width:36px;height:36px;background:#fff}
.footer-brand .brand-name{color:#fff}
.copyright{left:0;top:2697px;width:1200px;height:34px;background:#000;border-top:1px solid #333;color:#ddd;font-size:12px;display:flex;align-items:center;justify-content:center}
</style>
</head>
<body>

<!-- hero -->
<div class="abs hero" role="img" aria-label="Warmly lit luxury living room with staircase, a hand tapping a home control tablet in front"></div>
<div class="abs hero-band"></div>
<div class="abs hero-title">Welcom to <span>RM Installations</span></div>
<div class="abs hero-text">We expert in Automated Lighting Control Make your Home Safe &amp; Secure With our largest audio video control system</div>
<svg class="abs hero-arrows" width="34" height="26" viewBox="0 0 34 26"><path d="M11 3 3 13l8 10" fill="none" stroke="#888" stroke-width="3"/><path d="M23 3l8 10-8 10" fill="none" stroke="#fff" stroke-width="3"/></svg>

<nav class="abs nav">
  <div class="brand"><span class="brand-mark"></span><span class="brand-name">RM<br>Installations</span></div>
  <div class="nav-links">
    <a class="active">Home</a><a>Our Team</a><a>Products</a><a>Past Project</a><a>Service</a><a>Feedback</a><a>Contact Us</a>
  </div>
</nav>

<!-- services -->
<h2 class="abs heading services-title">Our <span>Services</span></h2>
<svg class="divider" style="left:485px;top:692px" width="230" height="24" viewBox="0 0 230 24"><line x1="0" y1="12" x2="230" y2="12" stroke="#ccc"/><rect x="96" y="6" width="12" height="12" fill="#bbb" transform="rotate(45 102 12)"/><rect x="109" y="5" width="14" height="14" fill="#666" transform="rotate(45 116 12)"/><rect x="124" y="6" width="12" height="12" fill="#bbb" transform="rotate(45 130 12)"/></svg>

<div class="side-arrow" style="left:52px"><svg width="16" height="16"><path d="M10 2 4 8l6 6" fill="none" stroke="#fff" stroke-width="3"/></svg></div>
<div class="side-arrow" style="left:1116px"><svg width="16" height="16"><path d="M6 2l6 6-6 6" fill="none" stroke="#fff" stroke-width="3"/></svg></div>

<div class="service-card" style="left:131px">
  <div class="service-photo" role="img" aria-label="Home theater media room with large screen" style="background:radial-gradient(ellipse 70px 40px at 120px 50px,#e8e6e0,rgba(232,230,224,0) 80%),linear-gradient(180deg,#1e1a18 0%,#3a2c22 55%,#6a4a32 100%)"></div>
  <div class="service-name">Media Rooms</div>
  <div class="service-text">Lor ipsumdolorsitac nsectetur adipiscing elit d.uis.</div>
  <div class="btn">View Details</div>
</div>
<div class="service-card" style="left:371px">
  <div class="service-photo" role="img" aria-label="Consultant reviewing designs on a laptop" style="background:radial-gradient(ellipse 60px 45px at 70px 70px,#f2f4f6,rgba(242,244,246,0) 80%),radial-gradient(ellipse 50px 60px at 150px 60px,#b08a6a,rgba(176,138,106,0) 80%),linear-gradient(135deg,#d8c8b0,#ece6dc 55%,#a89280)"></div>
  <div class="service-name">Design and Consultations</div>
  <div class="service-text">Lor ipsumdolorsitac nsectetur adipiscing elit d.uis.</div>
  <div class="btn">View Details</div>
</div>
<div class="service-card" style="left:614px">
  <div class="service-photo" role="img" aria-label="Room with blue automated ceiling lighting" style="background:radial-gradient(ellipse 55px 35px at 92px 70px,#6ab0ff,rgba(106,176,255,0) 85%),linear-gradient(180deg,#2a6ad0 0%,#0c1a36 25%,#0a0e18 70%,#1a1a1e 100%)"></div>
  <div class="service-name">Automated Lighting Control</div>
  <div class="service-text">Lor ipsumdolorsitac nsectetur adipiscing elit d.uis.</div>
  <div class="btn">View Details</div>
</div>
<div class="service-card" style="left:854px">
  <div class="service-photo" role="img" aria-label="Operator watching security camera monitors" style="background:radial-gradient(ellipse 40px 60px at 35px 70px,#2a2a30,rgba(42,42,48,0) 85%),linear-gradient(135deg,#8a96a2,#c4ccd4 50%,#5a646e)"></div>
  <div class="service-name">Security Camera Systems</div>
  <div class="service-text">Lor ipsumdolorsitac nsectetur adipiscing elit d.uis.</div>
  <div class="btn">View Details</div>
</div>

<!-- about -->
<section class="abs about"></section>
<h3 class="abs heading" style="left:133px;top:1095px;font-size:21px;color:#222">About <span style="color:#fff">RM Installations</span></h3>
<svg class="divider" style="left:133px;top:1137px" width="530" height="20" viewBox="0 0 530 20"><line x1="52" y1="10" x2="530" y2="10" stroke="#fff" stroke-opacity=".7"/><rect x="4" y="5" width="10" height="10" fill="#fff" transform="rotate(45 9 10)"/><rect x="18" y="3" width="14" height="14" fill="#222" transform="rotate(45 25 10)"/><rect x="36" y="5" width="10" height="10" fill="#fff" transform="rotate(45 41 10)"/></svg>
<div class="abs about-text">
  <p>Lorem ipsum dolor sit amet, consectetur adipiscing elit. Aenean et dignissim sem, interdum risus. Vestibulum consectetur nisi mollis diam pulvinar adipiscing. Vestibulum ut urna nec nibh adipiscing facilisis. Etiam auctor porta lacus ac luctus. Praesent ac libero fermentum, rhoncus magna a, dapibus mauris. Nam ut auctor justo. Sed ante odio, luctus quis nequ nec, adipiscing eleifend arcu. Integer nunc turpis, porttitor at lorem ut.</p>
  <p>Quisque hendrerit molestie commodo. Aliquam imperdiet varius tortor ut condiment Nulla ornare ultricies nunc et scelerisque. Class aptent taciti sociosqu ad litora torquent conubia nostra, per inceptos himenaeos. Mauris mattis ultrices diam nec luctus.</p>
</div>
<div class="btn" style="left:133px;top:1378px;width:110px;height:28px">Read More</div>

<h3 class="abs heading" style="left:741px;top:1095px;font-size:21px;color:#222">Past <span style="color:#fff">Project Videos</span></h3>
<svg class="divider" style="left:741px;top:1137px" width="328" height="20" viewBox="0 0 328 20"><line x1="52" y1="10" x2="328" y2="10" stroke="#fff" stroke-opacity=".7"/><rect x="4" y="5" width="10" height="10" fill="#fff" transform="rotate(45 9 10)"/><rect x="18" y="3" width="14" height="14" fill="#222" transform="rotate(45 25 10)"/><rect x="36" y="5" width="10" height="10" fill="#fff" transform="rotate(45 41 10)"/></svg>
<div class="abs video" role="img" aria-label="Video still of a bright living room and a phone remote"></div>
<div class="abs play"><svg width="52" height="36"><path d="M21 11v14l12-7z" fill="#fff"/></svg></div>
<div class="abs video-bar"><svg width="328" height="26"><rect x="14" y="8" width="3" height="10" fill="#fff"/><rect x="20" y="8" width="3" height="10" fill="#fff"/><rect x="34" y="12" width="200" height="3" fill="#4a8fd8"/><circle cx="174" cy="13" r="4" fill="#fff"/><rect x="270" y="12" width="40" height="3" fill="#888"/><circle cx="290" cy="13" r="6" fill="#fff"/></svg></div>
<div class="btn" style="left:741px;top:1378px;width:110px;height:28px">View More</div>

<!-- team -->
<h2 class="abs heading team-title">Our <span>Team</span></h2>
<svg class="divider" style="left:485px;top:1542px" width="230" height="24" viewBox="0 0 230 24"><line x1="0" y1="12" x2="230" y2="12" stroke="#ccc"/><rect x="96" y="6" width="12" height="12" fill="#bbb" transform="rotate(45 102 12)"/><rect x="109" y="5" width="14" height="14" fill="#666" transform="rotate(45 116 12)"/><rect x="124" y="6" width="12" height="12" fill="#bbb" transform="rotate(45 130 12)"/></svg>

<div class="member" style="left:133px"><div class="diamond"><div class="diamond-photo" role="img" aria-label="Portrait of a team member in a suit"></div></div></div>
<div class="member" style="left:373px"><div class="diamond"><div class="diamond-photo" role="img" aria-label="Portrait of a team member in a tuxedo"></div></div></div>
<div class="member" style="left:615px"><div class="diamond dark"><div class="diamond-photo" role="img" aria-label="Darkened portrait of a team member with social links"></div></div>
  <svg class="abs" style="left:56px;top:70px" width="100" height="70"><line x1="10" y1="8" x2="90" y2="8" stroke="#888"/><rect x="20" y="20" width="12" height="12" fill="#fff"/><rect x="38" y="20" width="12" height="12" fill="#fff"/><rect x="56" y="20" width="12" height="12" fill="#fff"/><rect x="74" y="20" width="12" height="12" fill="#fff"/><line x1="10" y1="44" x2="90" y2="44" stroke="#888"/></svg>
</div>
<div class="member" style="left:854px"><div class="diamond"><div class="diamond-photo" role="img" aria-label="Portrait of a smiling team member" style="background:radial-gradient(circle at 50% 50%,#f4e6d6 0%,#d8b898 40%,#8a6a50 85%)"></div></div></div>

<div class="member-name" style="left:119px">Evan Doyle</div>
<div class="member-name" style="left:359px">Marc Colter</div>
<div class="member-name active" style="left:601px">Nolan Hart</div>
<div class="member-name" style="left:840px">Jenna Lowell</div>
<div class="abs name-rule"></div>

<!-- products -->
<section class="abs products"></section>
<h2 class="abs heading products-title">Products <span>Brand With Us</span></h2>
<svg class="divider" style="left:485px;top:1993px" width="230" height="24" viewBox="0 0 230 24"><line x1="0" y1="12" x2="230" y2="12" stroke="#ccc"/><rect x="96" y="6" width="12" height="12" fill="#bbb" transform="rotate(45 102 12)"/><rect x="109" y="5" width="14" height="14" fill="#666" transform="rotate(45 116 12)"/><rect x="124" y="6" width="12" height="12" fill="#bbb" transform="rotate(45 130 12)"/></svg>
<svg class="abs" style="left:66px;top:2040px" width="16" height="28"><path d="M13 2 3 14l10 12" fill="none" stroke="#aaa" stroke-width="2"/></svg>
<svg class="abs" style="left:1118px;top:2040px" width="16" height="28"><path d="M3 2l10 12-10 12" fill="none" stroke="#aaa" stroke-width="2"/></svg>
<div class="abs brand-row">
  <span>Arcwell</span>
  <span>Phasor Audio</span>
  <span>Archline</span>
  <span><i></i>Centrix</span>
  <span><i></i>Genova</span>
  <span>Trellis</span>
</div>

<!-- feedback -->
<section class="abs feedback" role="img" aria-label="Dim background photo of a control room with screens"></section>
<h2 class="abs heading" style="left:133px;top:2160px;font-size:33px;color:#fff">Feedback</h2>
<svg class="divider" style="left:133px;top:2216px" width="605" height="20" viewBox="0 0 605 20"><line x1="52" y1="10" x2="605" y2="10" stroke="#777"/><rect x="4" y="5" width="10" height="10" fill="#aaa" transform="rotate(45 9 10)"/><rect x="18" y="3" width="14" height="14" fill="#f78f20" transform="rotate(45 25 10)"/><rect x="36" y="5" width="10" height="10" fill="#aaa" transform="rotate(45 41 10)"/></svg>
<div class="abs feedback-text">Lorem Ipsum is simply dummy text of the printing and typesetting industry. Lorem Ipsum has b industry's standard dummy text ever since the 1500s.</div>
<div class="field" style="left:133px;top:2319px;width:197px;height:30px">Name</div>
<div class="field" style="left:335px;top:2319px;width:197px;height:30px">Phone no</div>
<div class="field" style="left:539px;top:2319px;width:196px;height:30px">Email Id</div>
<div class="field" style="left:133px;top:2358px;width:602px;height:137px">Your Message</div>
<div class="submit">SUBMIT</div>

<h2 class="abs heading" style="left:797px;top:2160px;font-size:33px;color:#fff">Share <span>With Us</span></h2>
<svg class="divider" style="left:797px;top:2216px" width="275" height="20" viewBox="0 0 275 20"><line x1="52" y1="10" x2="275" y2="10" stroke="#777"/><rect x="4" y="5" width="10" height="10" fill="#aaa" transform="rotate(45 9 10)"/><rect x="18" y="3" width="14" height="14" fill="#f78f20" transform="rotate(45 25 10)"/><rect x="36" y="5" width="10" height="10" fill="#aaa" transform="rotate(45 41 10)"/></svg>
<div class="abs share-text">Lorem Ipsum is simply dummy text of t printing and typesetting industry.</div>
<div class="social" style="top:2313px"><i></i>Friendbook</div>
<div class="social" style="top:2376px"><i></i>Chirper</div>
<div class="social" style="top:2438px"><i></i>Linkpro</div>
<div class="social" style="top:2500px"><i><svg width="22" height="16"><rect x="1" y="1" width="20" height="14" fill="#fff"/><path d="M1 1l10 8 10-8" fill="none" stroke="#222" stroke-width="1.5"/></svg></i>Email</div>

<!-- footer -->
<footer class="abs footer"></footer>
<div class="footer-col" style="left:133px;top:2615px">
  <div class="row"><svg width="12" height="16"><path d="M6 15C2 9 1 7 1 5.5a5 5 0 0 1 10 0C11 7 10 9 6 15z" fill="#fff"/><circle cx="6" cy="5.5" r="2" fill="#000"/></svg>Contrary to popular belief,</div>
  <div style="padding-left:26px">Lorem Ipsum is.<br>1234567</div>
</div>
<div class="footer-col" style="left:518px;top:2615px">
  <div class="row"><svg width="14" height="14"><path d="M3 1l3 3-2 2c1 2 2 3 4 4l2-2 3 3-2 2C6 13 1 8 1 3z" fill="#fff"/></svg>Phone: 123 456 789</div>
  <div class="row"><svg width="14" height="14"><rect x="3" y="1" width="8" height="4" fill="#fff"/><rect x="1" y="5" width="12" height="6" fill="#fff"/><rect x="3" y="9" width="8" height="4" fill="#fff" stroke="#000"/></svg>Fax: 123 456 789</div>
  <div class="row"><svg width="14" height="12"><rect x="0" y="1" width="14" height="10" fill="#fff"/><path d="M0 1l7 5 7-5" fill="none" stroke="#000"/></svg>info@rminstall.example</div>
</div>
<div class="abs footer-brand"><span class="brand-mark"></span><span class="brand-name">RM<br>Installations</span></div>
<div class="abs copyright">Copyright © 2015 RM Installations. All Rights Reserved.</div>

</body>
</html>
```